Satchel & Sundial needs new business card design

I need a new business card design. I'm looking for out-of-the-box design which represents the freedom of being a location independent entrepreneur.
I offer coaching, retreats and trips.
I would like to see designs with and without the photo.
Colors I use are black (#000000), green (#25A796) and brown (#D7C38C)
Website satchelandsundial.example

Target Market(s)

location independent entrepreneurs, digital nomads, people looking to swap the 9 to 5 for a lifestyle business

Industry/Entity Type

Business

Contact Information for Business Card

Dorota Falkner
Your Lifestyle Business Coach, Retreat & Trip Leader
http://satchelandsundial.example
hello@satchelandsundial.example
Live a life you don't need a holiday from

Font styles to use
Serif
Sans Serif

Requirements
Must have
• One side should contain only the logo. I would also consider having the "Live a life you don't need a holiday from" on that side too (depending on how it looks)
• Please show both sides on the designs.

```html
<!DOCTYPE html>
<html lang="en">
<head>
<meta charset="utf-8">
<title>Satchel &amp; Sundial – Business Card</title>
<link rel="stylesheet" href="https://fonts.googleapis.com/css2?family=Montserrat:wght@400;500;600&family=Libre+Baskerville&display=swap">
<style>
  :root {
    --ink: #1a1a1a;
    --green: #25a796;
    --brown: #d7c38c;
    --paper: #ffffff;
    --backdrop: #2b2b2d;
    --photo-top: #6f8a55;
    --photo-bottom: #b9b29a;
  }
  * { box-sizing: border-box; margin: 0; padding: 0; }
  html, body { width: 1200px; height: 900px; overflow: hidden; }
  body {
    background: var(--backdrop);
    font-family: "Montserrat", sans-serif;
    color: var(--ink);
    position: relative;
  }
  .card {
    position: absolute;
    left: 280px;
    width: 640px;
    height: 366px;
    background: var(--paper);
    border-radius: 22px;
    overflow: hidden;
    box-shadow: 0 10px 26px rgba(0,0,0,.45);
  }
  .card--logo { top: 70px; }
  .card--contact { top: 464px; display: flex; }

  .logo-name {
    font-family: "Montserrat", sans-serif;
    font-weight: 600;
    color: var(--ink);
    text-transform: uppercase;
    letter-spacing: .04em;
    white-space: nowrap;
  }

  .card--logo .logo-name {
    position: absolute;
    top: 118px;
    left: 0; right: 0;
    text-align: center;
    font-size: 44px;
  }
  .motto {
    position: absolute;
    top: 232px;
    left: 0; right: 0;
    text-align: center;
    font-size: 15px;
    font-weight: 500;
    letter-spacing: .06em;
    text-transform: uppercase;
  }
  .site {
    position: absolute;
    top: 262px;
    left: 0; right: 0;
    text-align: center;
    font-size: 17px;
    font-weight: 500;
  }
  .site b, .contact-list b { color: var(--green); font-weight: 600; }

  .photo {
    width: 290px;
    height: 100%;
    background: linear-gradient(170deg, var(--photo-top) 0%, #8f9d6c 55%, var(--photo-bottom) 100%);
  }
  .details {
    flex: 1;
    padding: 40px 34px 0 20px;
    text-align: right;
  }
  .details .logo-name { font-size: 27px; }
  .person {
    margin-top: 30px;
    font-family: "Libre Baskerville", serif;
    font-size: 24px;
    color: var(--green);
  }
  .role {
    margin-top: 4px;
    font-size: 14px;
    line-height: 1.35;
  }
  .contact-list {
    list-style: none;
    margin-top: 26px;
    font-size: 14px;
    line-height: 1.75;
  }
  .contact-list li { display: flex; justify-content: flex-end; align-items: center; gap: 8px; }
  .contact-list svg { width: 12px; height: 12px; flex: none; }
</style>
</head>
<body>
  <section class="card card--logo">
    <h1 class="logo-name">Satchel &amp; Sundial</h1>
    <p class="motto">Live a life you don’t need a holiday from</p>
    <p class="site">www.<b>satchelandsundial</b>.example</p>
  </section>

  <section class="card card--contact">
    <div class="photo" role="img" aria-label="Photo of the coach sitting on a wooden rail among green trees"></div>
    <div class="details">
      <h2 class="logo-name">Satchel &amp; Sundial</h2>
      <p class="person">Dorota Falkner</p>
      <p class="role">Your Lifestyle Business Coach<br>Retreat &amp; Trip Leader</p>
      <ul class="contact-list">
        <li>+330 5550-1482
          <svg viewBox="0 0 12 12" aria-hidden="true"><path d="M3 1l2 2-1 1.5c.6 1.4 1.6 2.4 3 3L8.5 6.5l2 2L9.5 10.5C5.5 10 2 6.5 1.5 2.5z" fill="var(--green)"/></svg>
        </li>
        <li>hello@satchelandsundial.example
          <svg viewBox="0 0 12 12" aria-hidden="true"><rect x="1" y="2.5" width="10" height="7" rx="1" fill="none" stroke="var(--green)" stroke-width="1.2"/><path d="M1.5 3l4.5 3.5L10.5 3" fill="none" stroke="var(--green)" stroke-width="1.2"/></svg>
        </li>
        <li>www.<b>satchelandsundial</b>.example
          <svg viewBox="0 0 12 12" aria-hidden="true"><circle cx="6" cy="6" r="4.8" fill="none" stroke="var(--green)" stroke-width="1.2"/><path d="M1.2 6h9.6M6 1.2c-2 2.6-2 7 0 9.6M6 1.2c2 2.6 2 7 0 9.6" fill="none" stroke="var(--green)" stroke-width="1"/></svg>
        </li>
      </ul>
    </div>
  </section>
</body>
</html>
```